Business Card Design For A Renovation Contractor Company

We need a business card for a new company based in Singapore, our company name is "RB Tolvane". We are a renovation contractor that builds designs into reality. We build more of F&B restaurants, retail stores and commercial offices. We work very closely with designers. The final design should communicate to our client that we are a company that you can trust, that will plan and complete your project without giving you a headache. I like my client to remember my company as "RB". The beauty of SIMPLE is important.

Industry/Entity Type

Contractor

Requirements
Nice to have
• Black or Red base

```html
<!DOCTYPE html>
<html lang="en">
<head>
<meta charset="utf-8">
<title>RB Tolvane — Business Card</title>
<link rel="stylesheet" href="https://fonts.googleapis.com/css2?family=Source+Sans+3:wght@400;600;700&display=swap">
<style>
  :root {
    --brand-red: #e8202a;
    --ink: #161616;
    --paper: #ffffff;
    --muted: #3a3a3a;
    --divider: #888888;
    --backdrop: #ecebe8;
  }
  * { box-sizing: border-box; margin: 0; padding: 0; }
  html, body {
    width: 1200px; height: 720px; overflow: hidden;
    background: var(--backdrop);
    font-family: "Source Sans 3", "Myriad Pro", sans-serif;
  }
  .canvas {
    width: 1200px; height: 720px;
    display: flex; align-items: center; justify-content: center; gap: 48px;
  }
  .card {
    position: relative;
    width: 540px; height: 310px;
    overflow: hidden;
    box-shadow: 0 6px 18px rgba(0,0,0,.15);
  }

  /* Front */
  .card--front { background: var(--paper); }
  .wordmark {
    position: absolute; top: 0; left: 0; width: 100%; height: 160px;
    display: flex; align-items: center; justify-content: center; gap: 14px;
  }
  .wordmark__dot { width: 18px; height: 18px; border-radius: 50%; background: var(--brand-red); flex: none; }
  .wordmark__name {
    font-size: 48px; font-weight: 400; color: var(--ink);
    letter-spacing: 0.5px; line-height: 1;
  }

  .rule { position: absolute; left: 0; width: 100%; height: 2px; background: var(--ink); }
  .rule--upper { top: 160px; }
  .rule--lower { top: 290px; }

  .band { position: absolute; left: 0; width: 100%; background: var(--brand-red); }
  .band--name {
    top: 166px; height: 26px;
    color: var(--paper); font-size: 17px; text-align: center; line-height: 26px;
  }
  .band--name strong { font-weight: 700; }
  .band--footer { top: 270px; height: 16px; }

  .details {
    position: absolute; top: 196px; left: 0; width: 100%; height: 70px;
    display: grid; grid-template-columns: 1fr 1fr;
  }
  .address {
    text-align: right; padding-right: 16px; padding-top: 16px;
    font-size: 15px; line-height: 18px; color: var(--muted);
    border-right: 1.5px solid var(--divider);
  }
  .contacts { list-style: none; padding-left: 16px; padding-top: 3px; }
  .contacts li {
    display: flex; align-items: center; gap: 7px;
    font-size: 15px; line-height: 16px; color: var(--muted);
  }
  .contacts svg { width: 12px; height: 12px; flex: none; }

  /* Back */
  .card--back {
    background: var(--brand-red);
    display: flex; flex-direction: column; align-items: center; justify-content: center;
  }
  .monogram {
    display: flex; align-items: center; gap: 16px; margin-top: -20px;
  }
  .monogram__text {
    font-size: 120px; font-weight: 700; color: var(--ink); line-height: 1;
  }
  .monogram__dot { width: 26px; height: 26px; border-radius: 50%; background: var(--ink); }
  .web {
    position: absolute; bottom: 34px; left: 0; width: 100%;
    text-align: center; color: var(--paper);
    font-size: 17px; letter-spacing: 4px;
  }
</style>
</head>
<body>
<main class="canvas">

  <section class="card card--front" aria-label="Card front">
    <div class="wordmark">
      <span class="wordmark__dot"></span>
      <span class="wordmark__name">RB Tolvane</span>
    </div>

    <div class="rule rule--upper"></div>
    <div class="band band--name"><strong>Your Name,</strong> Title</div>

    <div class="details">
      <p class="address">Street Name<br>City Name<br>State Zip Code</p>
      <ul class="contacts">
        <li>
          <svg viewBox="0 0 12 12"><circle cx="6" cy="6" r="6" fill="var(--brand-red)"/><path d="M4 3.2c.4 0 .6.9.6 1.2 0 .3-.4.4-.3.7.3.7.8 1.2 1.5 1.5.3.1.4-.3.7-.3.3 0 1.2.2 1.2.6 0 .6-.6 1-1.1 1C4.8 7.9 4 7 3.1 4.3c0-.6.4-1.1.9-1.1z" fill="#fff"/></svg>
          123-456-0789
        </li>
        <li>
          <svg viewBox="0 0 12 12"><circle cx="6" cy="6" r="6" fill="var(--brand-red)"/><rect x="4.2" y="2.5" width="3.6" height="7" rx=".6" fill="#fff"/><rect x="4.8" y="3.3" width="2.4" height="4.2" fill="var(--brand-red)"/></svg>
          123-456-0789
        </li>
        <li>
          <svg viewBox="0 0 12 12"><circle cx="6" cy="6" r="6" fill="var(--brand-red)"/><rect x="3" y="4" width="6" height="4.2" fill="#fff"/><path d="M3 4l3 2.4L9 4" stroke="var(--brand-red)" stroke-width=".7" fill="none"/></svg>
          info@rbtolvane.com
        </li>
        <li>
          <svg viewBox="0 0 12 12"><circle cx="6" cy="6" r="6" fill="var(--brand-red)"/><circle cx="6" cy="6" r="3" fill="none" stroke="#fff" stroke-width=".8"/><path d="M3 6h6M6 3c-1.3 1.6-1.3 4.4 0 6M6 3c1.3 1.6 1.3 4.4 0 6" stroke="#fff" stroke-width=".6" fill="none"/></svg>
          www.rbtolvane.com
        </li>
      </ul>
    </div>

    <div class="band band--footer"></div>
    <div class="rule rule--lower"></div>
  </section>

  <section class="card card--back" aria-label="Card back">
    <div class="monogram">
      <span class="monogram__text">RB</span>
      <span class="monogram__dot"></span>
    </div>
    <p class="web">www.rbtolvane.com</p>
  </section>

</main>
</body>
</html>
```